Poetry Book Cover Design Project

Looking for a minimalistic book cover design for a collection of poems. The book title is "Before The Lanterns Drift Away Slowly". There are three parts to the book. First covers poetry in the theme of Rage. Second love and desire. The third is strange poems. Essentially the sections are "Rage", "Desire" and the "Strange". The reason for the title "Before The Lanterns Drift Away Slowly" is as if someone is writing these till life changes towards the intended outcome as felt in each poem. I want to have the author's name "Ruvinath Kolongaswe" at the bottom. Ilustration attached.
- Minimalistic

```html
<!DOCTYPE html>
<html lang="en">
<head>
<meta charset="utf-8">
<title>Before The Lanterns Drift Away Slowly — Cover Wrap</title>
<link rel="stylesheet" href="https://fonts.googleapis.com/css2?family=Special+Elite&family=EB+Garamond&display=swap">
<style>
  :root {
    --backdrop: #ececec;
    --paper: #ffffff;
    --ink: #111111;
    --body-ink: #2a2a2a;
    --art-dark: #3a4650;
    --art-mid: #6c7a82;
    --art-warm: #b79a84;
  }
  * { margin: 0; padding: 0; box-sizing: border-box; }
  html, body {
    width: 899px; height: 1200px; overflow: hidden;
    background: var(--backdrop);
  }
  .cover-wrap {
    position: absolute;
    left: 20px; top: 297px;
    width: 859px; height: 605px;
    background: var(--paper);
    box-shadow: 0 2px 8px rgba(0,0,0,0.18);
  }
  .back-blurb {
    position: absolute;
    left: 43px; top: 78px; width: 308px;
    font-family: "EB Garamond", serif;
    font-size: 10.3px; line-height: 12px;
    color: var(--body-ink);
    text-align: justify;
    hyphens: auto;
  }
  .spine-title, .spine-author {
    position: absolute;
    writing-mode: vertical-rl;
    font-family: "Special Elite", monospace;
    color: var(--ink);
    white-space: nowrap;
  }
  .spine-title { left: 428px; top: 53px; font-size: 10px; }
  .spine-author { left: 426px; top: 346px; font-size: 12.5px; }
  .front-title {
    position: absolute;
    right: 51px; top: 36px;
    font-family: "Special Elite", monospace;
    font-size: 37px; line-height: 39px;
    color: var(--ink);
    text-align: right;
    font-weight: 400;
  }
  .front-title span { display: block; }
  .feather-art {
    position: absolute;
    left: 501px; top: 275px;
    width: 296px; height: 250px;
  }
  .front-author {
    position: absolute;
    right: 51px; top: 536px;
    font-family: "Special Elite", monospace;
    font-size: 15px;
    color: var(--ink);
    letter-spacing: 0.3px;
    white-space: nowrap;
  }
</style>
</head>
<body>
  <main class="cover-wrap">
    <p class="back-blurb">Lorem ipsum dolor sit amet, consectetur adipiscing elit. Donec ligula magna, tempus eu auctor sit amet, pharetra ut velit. Curabitur euismod congue nibh quis feugiat. Vivamus in neque in erat lacinia consectetur. In a rhoncus metus. Sed fringilla eros tellus, finibus lobortis libero mattis ut. Maecenas urna neque, porttitor in mi et, porttitor auctor enim. Donec auctor at dolor sit amet dapibus. Proin luctus imperdiet nisi, in semper dui molestie vitae. Sed semper hendrerit tempor. Phasellus velit est, accumsan et molestie ut, condimentum ac erat. Nam aliquam ultricies leo vitae dictum. Morbi non nisi nec nisl vulputate imperdiet in in purus.</p>

    <div class="spine-title">Before The Lanterns Drift Away Slowly</div>
    <div class="spine-author">Ruvinath Kolongaswe</div>

    <h1 class="front-title">
      <span>Before</span>
      <span>The</span>
      <span>Lanterns</span>
      <span>Drift</span>
      <span>Away</span>
      <span>Slowly</span>
    </h1>

    <svg class="feather-art" viewBox="0 0 296 250" role="img" aria-label="Placeholder for the painted feather illustration">
      <defs>
        <linearGradient id="artTone" x1="0" y1="1" x2="1" y2="0">
          <stop offset="0" stop-color="var(--art-dark)"/>
          <stop offset="0.5" stop-color="var(--art-mid)"/>
          <stop offset="1" stop-color="var(--art-warm)"/>
        </linearGradient>
      </defs>
      <rect x="0" y="0" width="296" height="250" fill="url(#artTone)" opacity="0.35"/>
    </svg>

    <p class="front-author">Ruvinath Kolongaswe</p>
  </main>
</body>
</html>
```